Corwin Beacon Lighting - Commercial & Residential Landscape Lighting

Landscape Lighting Services & Design: Create a website for our landscape lighting company. We would like the design to be tailored around this description:
Illuminate with Confidence. Designed with Precision. Installed with Care.
Locally and veteran-owned, we take pride in transforming outdoor spaces through innovative lighting solutions tailored to your vision. From landscape and holiday lighting to permanent installations, our effortless process and expert design deliver breathtaking results and lasting curb appeal. Backed by a lifetime warranty and quarterly service options, our commitment to quality and customer satisfaction is unwavering. Try before you buy and experience your home in a whole new light with our complimentary demo kit — see the stunning effects before you decide.
- Also, add in this information as well; Outdoor Lighting not only beautifies spaces but also significantly enhances safety by illuminating your home or business. Beautifully lit entrances deter potential intruders, making your home a safer place for your loved ones. we also offer quarterly service plans to ensure lighting equipment continues to operate & illuminate effectively throughout the year. Also mention we provide free estimates and we are offering a 10% discount to military, veterans, and first responders.

Target Market(s)

Luxury market

Industry/Entity Type

Landscape Lighting - Residential & Commercial Lighting Services

Coding

Coded - Design and coding required

Number of Pages Required

2 page

Colors
00AB8E
00BBA5
67D7C9
C6EFE9
E9F9F6
59FF00
82FF00
B8FF75
E3FFCB
F4FFEA
FFC000
F8CF3A
FAE287
FDF2CF
FEFAEE

Requirements
Must have
• a lead generation button where people can submit their information for us to reach out to them and schedule their free estimate, homepage, about page, contact page, products and services page, user friendly, easy to navigate, and it also must be engaging and eye popping, as well as appealing to the luxury market. Please use colors; verdent green, dark green, ivory, and sunny yellow. Also, include an about page that references our story; Derek is retired Army and he opened a fitness studio in 2017 with his wife Jolene. He has installed low voltage lighting in every home he lived in and for his friends and family over the years and decided to open his own business because he is passionate about beautifying outdoor landscapes and highlighting a properties full potential, not only in the day but at night as well all while providing safety and security for his clients. Having a deep respect for nature and landscaping, he wants to provide the same care and quality to each of his clients as he has in the fitness industry for decades. He believes small businesses are the back bone of America and he's excited to provide a service that is all to often neglected in the design of a home.
Nice to have
• I would like to have a clear intent and purpose, engaging web design, clear call to action, optimized for search engines, mobile friendy design, security measures, credibility indicators

```html
<!DOCTYPE html>
<html lang="en">
<head>
<meta charset="utf-8">
<title>Corwin Beacon Lighting</title>
<link href="https://fonts.googleapis.com/css2?family=Kanit:wght@400;500;600&family=Mulish:wght@400;500;600;700&display=swap" rel="stylesheet">
<style>
:root{
  --teal:#1a9e88;
  --teal-dark:#12806d;
  --teal-light:#e8f6f4;
  --sun:#f8b31a;
  --ink:#1b1b1b;
  --body:#333;
  --ivory:#f4f3ec;
  --black:#000;
  --white:#fff;
}
*{margin:0;padding:0;box-sizing:border-box}
html,body{width:1200px;height:4268px;overflow:hidden}
body{position:relative;font-family:"Mulish",sans-serif;color:var(--body);background:var(--white)}
.abs{position:absolute}
.head{font-family:"Kanit",sans-serif;font-weight:500;color:var(--ink);letter-spacing:1px}
.btn{position:absolute;display:flex;align-items:center;justify-content:center;border-radius:30px;font-weight:700;color:var(--white);font-size:15px}
.btn-sun{background:var(--sun)}
.btn-teal{background:var(--teal)}
.rule{position:absolute;height:4px;width:56px;background:var(--teal)}
/* header */
.topbar{left:381px;top:0;width:819px;height:42px;background:var(--teal);clip-path:polygon(0 0,100% 0,100% 100%,34px 100%);display:flex;align-items:center;color:var(--white);font-size:16px;font-weight:600;gap:40px;padding-left:104px}
.brand{left:108px;top:14px;font-weight:700;color:var(--teal);font-size:24px;line-height:28px;display:flex;align-items:center;gap:10px}
.brand-dot{width:14px;height:14px;border-radius:50%;background:var(--sun)}
.nav{left:564px;top:60px;display:flex;gap:44px;font-size:15px;font-weight:600;color:var(--ink)}
.nav .on{color:var(--teal)}
/* hero */
.hero{left:0;top:95px;width:1200px;height:600px;background:radial-gradient(ellipse at 55% 45%,#8a6426 0%,#4a3f18 38%,#1c2812 72%,#0d160a 100%)}
.hero-title{left:0;width:1200px;text-align:center;color:var(--white);font-family:"Kanit",sans-serif;font-weight:600;font-size:44px;line-height:62px;top:380px}
.hero-text{left:0;width:1200px;text-align:center;color:var(--white);font-size:17px;line-height:31px;top:510px}
/* intro */
.intro-title{left:108px;top:803px;font-size:32px;line-height:47px}
.intro-title .hl{color:var(--teal)}
.intro-copy{left:613px;top:788px;width:450px;font-size:16px;line-height:29px;color:var(--ink)}
.intro-copy p+p{margin-top:29px}
.photo{position:absolute}
/* demo */
.demo{left:0;top:1554px;width:1200px;height:415px;background:linear-gradient(180deg,#1f7a60 0%,#168a72 100%)}
.demo-title{left:0;width:1200px;top:1680px;text-align:center;color:var(--white);font-size:32px;line-height:41px}
/* services */
.svc-card{position:absolute;top:2184px;width:284px}
.svc-img{height:190px;border-radius:12px}
.svc-icon{position:absolute;left:111px;top:159px;width:62px;height:62px;border-radius:50%;background:var(--white);box-shadow:0 2px 8px rgba(0,0,0,.15);display:flex;align-items:center;justify-content:center}
.svc-text{margin-top:58px;text-align:center;font-size:16px;font-weight:600;line-height:28px;color:var(--ink)}
/* story */
.story{left:0;top:2651px;width:1200px;height:600px;background:var(--teal-light)}
.story-text{left:630px;top:2840px;width:455px;font-size:14px;line-height:25.6px;color:var(--body)}
/* contact */
.contact{left:0;top:3251px;width:1200px;height:590px;background:var(--ivory)}
.c-icon{position:absolute;left:136px;width:80px;height:80px;border-radius:50%;background:var(--teal);display:flex;align-items:center;justify-content:center}
.c-label{position:absolute;left:244px;font-size:14px;line-height:26px;color:var(--ink)}
.c-label b{font-weight:700}
.field{position:absolute;background:var(--white);border:1px solid #e2e2e2;border-radius:4px;font-size:14px;color:#777;padding:14px 16px}
/* footer */
.footer{left:0;top:3841px;width:1200px;height:427px;background:var(--black)}
.f-head{position:absolute;top:3902px;font-weight:700;font-size:21px;color:var(--white)}
.f-list{position:absolute;top:3952px;list-style:none;font-size:15px;line-height:32.5px;color:var(--white)}
.f-list li::before{content:"➜";margin-right:12px;font-size:13px}
.social{position:absolute;top:4071px;width:30px;height:30px;border-radius:50%;background:var(--white)}
</style>
</head>
<body>

<!-- header -->
<div class="abs brand"><span class="brand-dot"></span>Corwin Beacon<br>Lighting</div>
<div class="abs topbar">
  <span>&#9990;&nbsp; PHONE: +1 555 014 2788</span>
  <span>&#9993;&nbsp; EMAIL: info@corwinbeacon.com</span>
  <svg width="18" height="18" viewBox="0 0 18 18"><circle cx="7.5" cy="7.5" r="5.5" fill="none" stroke="#fff" stroke-width="2.4"/><line x1="11.5" y1="11.5" x2="16" y2="16" stroke="#fff" stroke-width="2.6"/></svg>
</div>
<nav class="abs nav"><span class="on">HOME</span><span>ABOUT US</span><span>PRODUCTS</span><span>SERVICES</span><span>CONTACT</span></nav>

<!-- hero -->
<div class="abs hero" role="img" aria-label="Night view of a home and garden bridge glowing with warm landscape lighting"></div>
<h1 class="abs hero-title">WELCOME TO<br>CORWIN BEACON LIGHTING</h1>
<p class="abs hero-text">Lorem ipsum dolor sit amet, consectetur adipiscing elit, sed do eiusmod<br>tempor incididunt ut labore et dolore magna aliqua.</p>
<div class="btn btn-sun" style="left:526px;top:585px;width:149px;height:47px">GET STARTED</div>

<!-- intro -->
<h2 class="abs head intro-title"><span class="hl">ILLUMINATE WITH<br>CONFIDENCE.</span><br>DESIGNED WITH PRECISION.<br>INSTALLED WITH CARE.</h2>
<div class="rule" style="left:108px;top:1000px;width:96px"></div>
<div class="abs intro-copy">
  <p>Locally and veteran-owned, we take pride in transforming outdoor spaces through innovative lighting solutions tailored to your vision.</p>
  <p style="font-size:15px">From landscape and holiday lighting to permanent installations, our effortless process and expert design deliver breathtaking results and lasting curb appeal. Backed by a lifetime warranty and quarterly service options, our commitment to quality and customer satisfaction is unwavering.</p>
</div>
<div class="photo" style="left:365px;top:1120px;width:725px;height:344px;background:linear-gradient(160deg,#3a4450 0%,#6e4030 40%,#a87a50 58%,#2a3422 100%)" role="img" aria-label="Brick house at dusk with uplit facade and garden lights"></div>
<div class="photo" style="left:107px;top:1068px;width:460px;height:320px;background:#fff;padding:4px">
  <div style="width:100%;height:100%;background:linear-gradient(180deg,#2e2f22 0%,#8a7040 45%,#4f5a28 70%,#5a6a2a 100%)" role="img" aria-label="House with lit front lawn at twilight"></div>
</div>

<!-- demo -->
<div class="abs demo" role="img" aria-label="Garden path with lighting under a green overlay"></div>
<h2 class="abs head demo-title">TRY BEFORE YOU BUY AND EXPERIENCE YOUR<br>HOME IN A WHOLE NEW LIGHT WITH OUR<br>COMPLIMENTARY DEMO KIT</h2>
<div class="btn btn-sun" style="left:400px;top:1832px;width:400px;height:46px;font-size:15px">SEE THE STUNNING EFFECTS BEFORE YOU DECIDE</div>

<!-- services -->
<h2 class="abs head" style="left:0;width:1200px;top:2092px;text-align:center;font-size:31px">SERVICE-FOCUSED</h2>
<div class="rule" style="left:570px;top:2140px;width:60px"></div>

<div class="svc-card" style="left:121px">
  <div class="svc-img" style="background:linear-gradient(180deg,#0f2a70 0%,#1d3a8a 50%,#5a3a20 100%)" role="img" aria-label="Pool area with trees lit at night"></div>
  <div class="svc-icon"><svg width="26" height="26" viewBox="0 0 26 26"><path d="M5 13 L11 19 L21 7" fill="none" stroke="#1a9e88" stroke-width="2.4"/></svg></div>
  <p class="svc-text">Outdoor Lighting not only<br>beautifies spaces but<br>also significantly enhances<br>safety by illuminating your<br>home or business.</p>
</div>
<div class="svc-card" style="left:456px">
  <div class="svc-img" style="background:linear-gradient(180deg,#3a3028 0%,#4a5a3a 50%,#7a5a8a 100%)" role="img" aria-label="Lit stone entrance path with colored lights"></div>
  <div class="svc-icon"><svg width="26" height="26" viewBox="0 0 26 26"><path d="M5 13 L11 19 L21 7" fill="none" stroke="#1a9e88" stroke-width="2.4"/></svg></div>
  <p class="svc-text">Beautifully lit entrances deter<br>potential intruders, making<br>your home a safer place for<br>your loved ones.</p>
</div>
<div class="svc-card" style="left:792px">
  <div class="svc-img" style="background:linear-gradient(180deg,#1a3a7a 0%,#2a4a3a 55%,#8aa040 100%)" role="img" aria-label="Palm and trees lit in a garden at night"></div>
  <div class="svc-icon"><svg width="26" height="26" viewBox="0 0 26 26"><path d="M5 13 L11 19 L21 7" fill="none" stroke="#1a9e88" stroke-width="2.4"/></svg></div>
  <p class="svc-text">we also offer quarterly service<br>plans to ensure lighting<br>equipment continues to operate<br>&amp; illuminate effectively<br>throughout the year.</p>
</div>

<!-- story -->
<div class="abs story"></div>
<div class="abs" style="left:151px;top:2751px;width:404px;height:404px;border-radius:50%;border:4px solid var(--teal)"></div>
<div class="abs" style="left:170px;top:2770px;width:366px;height:366px;border-radius:50%;background:linear-gradient(160deg,#e4e6e8 0%,#b8bcc0 45%,#3c4450 100%)" role="img" aria-label="Portrait of the founder in a suit"></div>
<h2 class="abs head" style="left:630px;top:2760px;font-size:31px;font-weight:600">OUR STORY</h2>
<div class="rule" style="left:630px;top:2808px;width:72px"></div>
<p class="abs story-text">Derek is retired Army and he opened a fitness studio in 2017 with his wife Jolene. He has installed low voltage lighting in every home he lived in and for his friends and family over the years and decided to open his own business because he is passionate about beautifying outdoor landscapes and highlighting a properties full potential, not only in the day but at night as well all while providing safety and security for his clients. Having a deep respect for nature and landscaping, he wants to provide the same care and quality to each of his clients as he has in the fitness industry for decades.</p>
<div class="btn btn-teal" style="left:630px;top:3090px;width:137px;height:45px;font-size:14px">LEARN MORE</div>

<!-- contact -->
<div class="abs contact"></div>
<h2 class="abs head" style="left:0;width:1200px;top:3362px;text-align:center;font-size:31px;font-weight:600">CONTACT US</h2>
<div class="rule" style="left:568px;top:3410px;width:66px"></div>

<div class="c-icon" style="top:3440px"><svg width="36" height="26" viewBox="0 0 36 26"><rect x="1" y="1" width="34" height="24" rx="2" fill="#fff"/><path d="M1 2 L18 15 L35 2" fill="none" stroke="#1a9e88" stroke-width="2.5"/></svg></div>
<div class="c-label" style="top:3456px"><b>EMAIL:</b><br>hello@corwinbeacon.com</div>
<div class="c-icon" style="top:3542px"><svg width="34" height="34" viewBox="0 0 24 24"><path d="M6.6 10.8a15 15 0 0 0 6.6 6.6l2.2-2.2c.3-.3.7-.4 1-.2 1.1.4 2.3.6 3.6.6.6 0 1 .4 1 1V20c0 .6-.4 1-1 1A17 17 0 0 1 3 4c0-.6.4-1 1-1h3.5c.6 0 1 .4 1 1 0 1.3.2 2.5.6 3.6.1.3 0 .7-.2 1z" fill="#fff"/></svg></div>
<div class="c-label" style="top:3558px"><b>PHONE:</b><br>+1 555 014 2788</div>
<div class="c-icon" style="top:3646px"><svg width="30" height="38" viewBox="0 0 24 30"><path d="M12 2a9 9 0 0 0-9 9c0 7 9 16 9 16s9-9 9-16a9 9 0 0 0-9-9z" fill="none" stroke="#fff" stroke-width="2.4"/><circle cx="12" cy="11" r="3.4" fill="none" stroke="#fff" stroke-width="2.4"/></svg></div>
<div class="c-label" style="top:3656px"><b>ADDRESS:</b><br>418 Larkspur Ave. #204<br>Ridgeview, CA 90412</div>

<div class="field" style="left:484px;top:3440px;width:283px;height:48px">First Name</div>
<div class="field" style="left:777px;top:3440px;width:283px;height:48px">Last Name</div>
<div class="field" style="left:484px;top:3501px;width:283px;height:48px">Phone Number</div>
<div class="field" style="left:777px;top:3501px;width:283px;height:48px">Email</div>
<div class="field" style="left:484px;top:3566px;width:576px;height:110px">Message</div>
<div class="btn btn-teal" style="left:484px;top:3698px;width:131px;height:45px;font-size:17px">Submit</div>

<!-- footer -->
<div class="abs footer"></div>
<div class="abs" style="left:118px;top:3960px;display:flex;align-items:center;gap:10px;font-weight:700;font-size:28px;line-height:34px;color:var(--sun)"><span style="width:16px;height:16px;border-radius:50%;background:var(--sun)"></span>Corwin Beacon<br>Lighting</div>
<div class="social" style="left:126px"></div>
<div class="social" style="left:171px"></div>
<div class="social" style="left:216px"></div>
<div class="social" style="left:262px"></div>

<div class="f-head" style="left:424px">Quick Links</div>
<ul class="f-list" style="left:428px"><li>Home</li><li>About Us</li><li>Services</li><li>Product</li><li>Contact Us</li></ul>
<div class="f-head" style="left:615px">Other Links</div>
<ul class="f-list" style="left:617px;line-height:30.5px"><li>FAQ</li><li>Tems of Use</li><li>Privacy Policy</li><li>Support Links</li><li>Conditions</li></ul>
<div class="f-head" style="left:812px">Sign Up To Our Newsletter</div>
<p class="abs" style="left:813px;top:3952px;width:290px;font-size:14px;line-height:31px;color:var(--white)">Lorem ipsum dolor sit amet,consectetur adipiscing elit,adipiscing elit.</p>
<div class="abs" style="left:815px;top:4020px;width:270px;padding-bottom:8px;border-bottom:2px solid var(--white);font-size:14px;color:var(--white)">Email</div>
<div class="btn" style="left:820px;top:4083px;width:146px;height:50px;background:var(--white);color:var(--teal);font-size:17px">Subscribe</div>
<div class="abs" style="left:100px;top:4205px;width:1003px;height:1px;background:#666"></div>
<p class="abs" style="left:0;width:1200px;top:4226px;text-align:center;font-size:14px;color:var(--white)">Copyrights@2025.Corwin Beacon Lighting.All Rights Reserved</p>

</body>
</html>
```